We need a business card design for a new company located in Missouri City, TX, entitled 'BrightPath Chiropractic & Holistic Center'. Our services include restoration of health and vitality, spinal exam, health assessment, dietary & fitness programs, lymphatic & therapeutic massage, detox & remineralize body wraps, far infrared sauna therapy

Industry/Entity Type

Business

Contact Information for Business Card

BrightPath Chiropractic & Holistic Center, Marlene Okafor LMT, 4215 Elm Ridge Rd., Suite 310, Missouri City, TX 77482, 281-555-0193

```html
<!DOCTYPE html>
<html lang="en">
<head>
<meta charset="utf-8">
<title>BrightPath Chiropractic &amp; Holistic Center — Business Card</title>
<link href="https://fonts.googleapis.com/css2?family=Open+Sans:wght@400;600&family=Tinos:wght@400;700&display=swap" rel="stylesheet">
<style>
  :root {
    --page: #e9e7e4;
    --card: #1f2022;
    --card-edge: #2a2b2e;
    --teal: #1fa596;
    --blue: #1f8fd3;
    --grey: #8d8f93;
    --white: #f2f2f2;
  }
  * { margin: 0; padding: 0; box-sizing: border-box; }
  html, body { width: 1200px; height: 780px; overflow: hidden; background: var(--page); }
  body { position: relative; font-family: "Open Sans", Arial, sans-serif; }

  .card {
    position: absolute;
    width: 560px; height: 320px;
    background: var(--card);
    border: 1px solid var(--card-edge);
    border-radius: 6px;
    overflow: hidden;
    box-shadow: 0 10px 30px rgba(0,0,0,.25);
  }
  .card--front { left: 30px; top: 160px; }
  .card--back { left: 610px; top: 300px; }

  /* Front */
  .brand { position: absolute; left: 34px; top: 58px; width: 220px; }
  .brand__row { display: flex; align-items: center; gap: 10px; }
  .brand__dot { width: 22px; height: 22px; border-radius: 50%; background: var(--teal); }
  .brand__name { font-family: "Tinos", "Times New Roman", serif; font-weight: 700; font-size: 34px; color: var(--grey); letter-spacing: .5px; }
  .brand__tagline { margin-top: 6px; font-size: 13px; color: var(--grey); letter-spacing: 1px; }

  .divider-v { position: absolute; left: 288px; top: 40px; width: 1px; height: 170px; background: var(--teal); }

  .person { position: absolute; left: 312px; top: 46px; }
  .person__name { font-family: "Tinos", "Times New Roman", serif; font-size: 32px; color: var(--teal); line-height: 1; }
  .person__role { font-family: "Tinos", "Times New Roman", serif; font-size: 17px; color: var(--white); margin-top: 4px; }

  .contacts { position: absolute; left: 312px; top: 128px; list-style: none; }
  .contacts li { display: flex; align-items: center; gap: 10px; font-size: 15px; color: var(--white); line-height: 26px; }
  .contacts svg { width: 14px; height: 14px; flex: none; }

  .divider-h { position: absolute; left: 0; right: 0; top: 232px; height: 1px; background: var(--teal); }
  .address { position: absolute; left: 34px; top: 246px; font-size: 14px; color: var(--white); }

  /* Back */
  .services__head { position: absolute; left: 30px; top: 28px; display: flex; align-items: center; gap: 12px; }
  .services__dot { width: 28px; height: 28px; border-radius: 50%; background: var(--teal); }
  .services__title { font-size: 40px; color: var(--blue); line-height: 1; }
  .services__rule { position: absolute; left: 80px; right: 0; top: 86px; height: 1px; background: var(--teal); }
  .services__list { position: absolute; left: 58px; top: 100px; list-style: none; }
  .services__list li { display: flex; align-items: center; gap: 14px; font-size: 19px; color: var(--white); line-height: 29px; }
  .services__list li::before { content: ""; width: 9px; height: 9px; border-radius: 50%; background: var(--white); flex: none; }
</style>
</head>
<body>

<section class="card card--front" aria-label="Business card front">
  <div class="brand">
    <div class="brand__row">
      <span class="brand__dot"></span>
      <span class="brand__name">BrightPath</span>
    </div>
    <p class="brand__tagline">Chiropractic &amp; Holistic Center</p>
  </div>

  <div class="divider-v"></div>

  <div class="person">
    <p class="person__name">Daniel Reyes</p>
    <p class="person__role">President</p>
  </div>

  <ul class="contacts">
    <li>
      <svg viewBox="0 0 14 14" aria-hidden="true"><rect width="14" height="14" rx="2" fill="#1fa596"/><path d="M4 3.5c.6 3 2.8 5.6 6 7l1-1.6-1.8-1-.8.8c-1-.6-1.8-1.5-2.3-2.5l.8-.8-1-1.8z" fill="#1f2022"/></svg>
      281-555-0193
    </li>
    <li>
      <svg viewBox="0 0 14 14" aria-hidden="true"><rect width="14" height="14" rx="2" fill="#1fa596"/><circle cx="7" cy="7" r="4" fill="none" stroke="#1f2022" stroke-width="1.2"/><path d="M3 7h8M7 3c-2 2.5-2 5.5 0 8M7 3c2 2.5 2 5.5 0 8" fill="none" stroke="#1f2022" stroke-width="1"/></svg>
      www.brightpathcenter.com
    </li>
    <li>
      <svg viewBox="0 0 14 14" aria-hidden="true"><rect width="14" height="14" rx="2" fill="#1fa596"/><rect x="3" y="4.5" width="8" height="5.5" fill="none" stroke="#1f2022" stroke-width="1.1"/><path d="M3 4.5l4 3 4-3" fill="none" stroke="#1f2022" stroke-width="1.1"/></svg>
      hello@brightpathcenter.com
    </li>
  </ul>

  <div class="divider-h"></div>
  <p class="address">Marlene Okafor LMT, 4215 Elm Ridge Rd., Suite 310, Missouri City, TX 77482</p>
</section>

<section class="card card--back" aria-label="Business card back">
  <div class="services__head">
    <span class="services__dot"></span>
    <h2 class="services__title">services</h2>
  </div>
  <div class="services__rule"></div>
  <ul class="services__list">
    <li>dietary &amp; fitness programs</li>
    <li>lymphatic &amp; therapeutic massage</li>
    <li>spinal exam</li>
    <li>health assessment</li>
    <li>far infrared sauna therapy</li>
    <li>restoration of health and vitality</li>
    <li>detox &amp; remineralize body wraps</li>
  </ul>
</section>

</body>
</html>
```